Complete the Quillmark Holdings Inc. business card as started in the attached files.

See the attached card for the starting point.

Font is attached (File #3). The "F" box is a capital F on the font set, and the "Se" box is the number 4 on the font set.

I would like to see variations of the image provided (File #2). Image provided does not have proper balance of the boxes to the following letters (i.e. "F" is in a different plane than "uillmark", and "Se" is in the plane). Create the background to match the "drifting cold" example (File #1).

Completion of the work will be source files for TWO cards. One with no title under my name, and one with the title Junior Deputy Assistant to the Regional Associate Vice President.

With thanks,

Lou

Target Market(s)

Science nerds

Industry/Entity Type

Business

Requirements
Must have
• Green colour; if the background can match the pattern of the "drifting cold" background that is fantastic.
Must use the Font attached for the logo name. See notes in the brief.

```html
<!DOCTYPE html>
<html lang="en">
<head>
<meta charset="utf-8">
<title>Quillmark Holdings Inc. — Business Cards</title>
<link href="https://fonts.googleapis.com/css2?family=Questrial&family=Roboto+Condensed:wght@400;700&display=swap" rel="stylesheet">
<style>
  :root {
    --page-bg: #d4d5d8;
    --card-green: #0b5426;
    --card-green-deep: #06441c;
    --haze-green: #2e7d45;
    --haze-dark: #043515;
    --rule-green: #2f9a4a;
    --frame-line: rgba(255, 255, 255, 0.22);
    --ink-white: #ffffff;
  }
  html, body {
    margin: 0;
    padding: 0;
    width: 1200px;
    height: 898px;
    overflow: hidden;
    background: var(--page-bg);
  }
  .card-sheet {
    position: relative;
    width: 1200px;
    height: 898px;
  }
  .business-card {
    position: absolute;
    left: 233px;
    width: 734px;
    height: 420px;
    overflow: hidden;
    background: var(--card-green);
    box-shadow: 0 8px 22px rgba(0, 0, 0, 0.25);
    color: var(--ink-white);
  }
  .card-titled { top: 20px; }
  .card-untitled { top: 458px; }
  .smoke-background {
    position: absolute;
    inset: 0;
    background:
      radial-gradient(ellipse 55% 45% at 20% 30%, rgba(46, 125, 69, 0.55), transparent 70%),
      radial-gradient(ellipse 50% 40% at 78% 70%, rgba(46, 125, 69, 0.45), transparent 70%),
      radial-gradient(ellipse 60% 50% at 60% 15%, rgba(4, 53, 21, 0.55), transparent 70%),
      linear-gradient(160deg, var(--card-green) 0%, var(--card-green-deep) 100%);
  }
  .card-frame {
    position: absolute;
    inset: 12px;
    border: 1px solid var(--frame-line);
  }
  .brand {
    position: absolute;
    left: 45px;
    top: 50px;
    display: flex;
    align-items: center;
    gap: 14px;
  }
  .brand-square {
    width: 52px;
    height: 52px;
    background: var(--ink-white);
    opacity: 0.35;
  }
  .brand-name {
    font-family: "Roboto Condensed", sans-serif;
    font-weight: 700;
    font-size: 40px;
    line-height: 1;
  }
  .holder {
    position: absolute;
    left: 45px;
    bottom: 55px;
    font-family: "Roboto Condensed", sans-serif;
  }
  .holder-name {
    margin: 0;
    font-weight: 700;
    font-size: 30px;
    letter-spacing: 0.4px;
    text-transform: uppercase;
  }
  .holder-title {
    margin: 4px 0 0;
    font-weight: 700;
    font-size: 15px;
    line-height: 1.25;
  }
  .divider {
    position: absolute;
    left: 410px;
    top: 140px;
    width: 2px;
    height: 140px;
    background: var(--rule-green);
  }
  .contact {
    position: absolute;
    left: 438px;
    top: 132px;
    font-family: "Questrial", sans-serif;
    font-size: 17px;
    line-height: 1.25;
  }
  .contact-company {
    margin: 0 0 6px;
    font-family: "Roboto Condensed", sans-serif;
    font-weight: 700;
    font-size: 21px;
  }
  .contact-address, .contact-lines { margin: 0; }
  .contact-lines { margin-top: 13px; }
</style>
</head>
<body>
  <div class="card-sheet">

    <div class="business-card card-titled">
      <div class="smoke-background" role="img" aria-label="Soft drifting smoke pattern in deep green tones"></div>
      <div class="card-frame"></div>
      <div class="brand">
        <div class="brand-square"></div>
        <div class="brand-name">Quillmark<br>Holdings</div>
      </div>
      <div class="holder">
        <p class="holder-name">Louis Kessling</p>
        <p class="holder-title">Junior Deputy Assistant to the<br>Regional Associate Vice President</p>
      </div>
      <div class="divider"></div>
      <div class="contact">
        <p class="contact-company">Quillmark Holdings Inc.</p>
        <p class="contact-address">218, 40117 Range Road 164<br>Brightwater, AB T4X 2K9</p>
        <p class="contact-lines">Ph: 780.555.0142<br>lou@quillmark.ca<br>www.quillmark.ca</p>
      </div>
    </div>

    <div class="business-card card-untitled">
      <div class="smoke-background" role="img" aria-label="Soft drifting smoke pattern in deep green tones"></div>
      <div class="card-frame"></div>
      <div class="brand">
        <div class="brand-square"></div>
        <div class="brand-name">Quillmark<br>Holdings</div>
      </div>
      <div class="holder">
        <p class="holder-name">Louis Kessling</p>
      </div>
      <div class="divider"></div>
      <div class="contact">
        <p class="contact-company">Quillmark Holdings Inc.</p>
        <p class="contact-address">218, 40117 Range Road 164<br>Brightwater, AB T4X 2K9</p>
        <p class="contact-lines">Ph: 780.555.0142<br>lou@quillmark.ca<br>www.quillmark.ca</p>
      </div>
    </div>

  </div>
</body>
</html>
```